Business Card for a Life Coaching Company

MOSSVALE is a Life Coaching company that was initiated to support people who want to transform thier life or ana aspect of it.
our slogan is : "Dream. Believe. Succeed"
our logo is uploaded.
The name of the company implies that leadership, strength and wisdom required to change your life.
We want an attractive business card that would give an impression of reliability, support and change. so we really want it unique. Here are some examples of unique cards:

http://www.pixelharbornotes.example/2009/05/100-really-creative-business-cards/

MossVale is a life coaching organization focusing on individual transformation through the application of relevant and timeless principles of success.  MossVale believes that real, sustainable life transformations are brought about by tuning into the timeless wisdom we each carry in our hearts while boldy acting in the direction of our dreams.

Contacts on the card:
Address: 7 Tarek Ibn Nabil Heliopolis Cairo Egypt
Tel: +202 24 81 37 52
Fax: +202 24 81 37 19
Mobile: +2 012 574 9026 (Nadia Sherif)
+2 0199915815 (Kamal Rashidi)

By the way, our temporary website is http://www.mossvale.example

We have attached an .eps file with various configurations of our logo.

```html
<!DOCTYPE html>
<html lang="en">
<head>
<meta charset="utf-8">
<title>MossVale — Business Card</title>
<link rel="stylesheet" href="https://fonts.googleapis.com/css2?family=Cinzel:wght@400;500&display=swap">
<style>
  :root {
    --card-brown: #573d2e;
    --slogan-orange: #f4884a;
    --name-cream: #f3e6a2;
    --art-light: #f4a468;
    --art-mid: #e07a3a;
    --art-deep: #b4561f;
  }
  html, body {
    margin: 0;
    padding: 0;
    width: 1200px;
    height: 720px;
    overflow: hidden;
    background: var(--card-brown);
  }
  .card {
    position: relative;
    width: 1200px;
    height: 720px;
    background: var(--card-brown);
    overflow: hidden;
  }
  .slogan {
    position: absolute;
    left: 96px;
    top: 100px;
    margin: 0;
    font-family: "Cinzel", "Trajan Pro", serif;
    font-weight: 500;
    color: var(--slogan-orange);
    font-size: 136px;
    line-height: 128px;
    letter-spacing: -2px;
    transform: scaleX(0.82);
    transform-origin: left top;
  }
  .slogan span {
    display: block;
  }
  .company-name {
    position: absolute;
    left: 98px;
    top: 500px;
    margin: 0;
    font-family: "Cinzel", "Trajan Pro", serif;
    font-weight: 400;
    font-size: 34px;
    line-height: 40px;
    color: var(--name-cream);
    letter-spacing: 0.95em;
    white-space: nowrap;
  }
  .brand-art {
    position: absolute;
    right: 0;
    top: 0;
    width: 400px;
    height: 720px;
  }
</style>
</head>
<body>
  <main class="card">
    <h1 class="slogan">
      <span>Believe</span>
      <span>Dream</span>
      <span>Succeed</span>
    </h1>
    <p class="company-name">MOSS VALE</p>
    <svg class="brand-art" viewBox="0 0 400 720" role="img" aria-label="Copper-toned brand illustration in profile facing left">
      <defs>
        <linearGradient id="artTone" x1="0" y1="0" x2="1" y2="1">
          <stop offset="0" stop-color="var(--art-light)"/>
          <stop offset="0.55" stop-color="var(--art-mid)"/>
          <stop offset="1" stop-color="var(--art-deep)"/>
        </linearGradient>
      </defs>
      <rect x="0" y="0" width="400" height="720" fill="url(#artTone)" opacity="0.9"/>
    </svg>
  </main>
</body>
</html>
```